Corinnehabbard.com

1. Conceptualization and designing of the site Homepage. The Homepage design will be completely customized and based on your design instructions (i.e. preferred colors, links to reference sites that you want us to take reference from if any etc) and the recently completed logo design.
2. Upon homepage design approval, based on it we will be creating the layout for the other 4 site inner pages (i.e. About page, Contact page, Services page, and Insights (publications, media).
3. Once all the inner page designs are approved, we will get the designs built (will make sure that the site is completely Responsive - works on all devices) within your provided WIX account.
4. We will add the static text and images provided by you to the Home page, About page, Contact page, and the Services page. For the 2 Insights sub-pages, we will add 1-2 sample Publications and Media entries.
once you confirm the total number of required entries for the 2 sub-pages, I will accordingly quote you on the same
5. Integration of a Contact form on the Contact page that will email the filled in details to your mail id.

```html
<!DOCTYPE html>
<html lang="en">
<head>
<meta charset="utf-8">
<title>Corinne Habbard Consulting</title>
<link href="https://fonts.googleapis.com/css2?family=Montserrat:wght@400;500;600;700;800&display=swap" rel="stylesheet">
<style>
:root{
  --green:#1f9b49;
  --blue:#0a9be0;
  --orange:#ef8a00;
  --ink:#111111;
  --text:#444444;
  --white:#ffffff;
  --light:#f2f3f3;
}
*{box-sizing:border-box;margin:0;padding:0}
html,body{width:1200px;height:3692px;overflow:hidden}
body{position:relative;font-family:'Montserrat',sans-serif;color:var(--text);background:var(--white)}
.abs{position:absolute}
/* top bar */
.topbar{left:0;top:0;width:1200px;height:44px;background:var(--green);color:var(--white);font-size:13px}
.topbar .item{top:14px;display:flex;align-items:center;gap:8px}
.topbar b{font-weight:700}
.social{top:8px;width:30px;height:30px;border-radius:50%;background:var(--white)}
/* nav */
.nav{left:0;top:44px;width:1200px;height:76px;background:var(--white)}
.nav a{position:absolute;top:33px;font-size:15px;color:#222;text-decoration:none;font-weight:500}
.nav a.active{color:var(--green)}
.brand-cap{left:535px;top:-8px;width:130px;height:90px;background:var(--white);border-radius:65px 65px 0 0;z-index:3}
.brand-mark{left:563px;top:4px;width:74px;height:74px;border-radius:50%;border:3px solid var(--blue);z-index:4}
.brand-name{left:450px;top:82px;width:300px;text-align:center;color:var(--blue);font-weight:700;font-size:19px;line-height:20px;z-index:4;letter-spacing:.5px}
.brand-name span{display:block;font-size:13px;letter-spacing:3px}
/* hero */
.hero{left:0;top:120px;width:1200px;height:640px}
.hero-photo{left:0;top:0;width:1200px;height:600px;background:linear-gradient(100deg,#1b1612 0%,#2e2620 40%,#4a3a30 62%,#1f3f8a 78%,#3a2f28 100%)}
.hero h1{left:112px;top:108px;color:var(--white);font-weight:800;font-size:45px;line-height:51px;letter-spacing:1.5px}
.hero p{left:112px;top:282px;width:490px;color:var(--white);font-size:15px;line-height:21px}
.btn{display:flex;align-items:center;justify-content:center;font-weight:700;border-radius:22px}
.hero .btn{left:112px;top:373px;width:150px;height:40px;background:var(--white);color:var(--ink);font-size:15px}
/* section titles */
.kicker{font-size:16px;font-weight:700;letter-spacing:2px;display:flex;align-items:center;gap:22px}
.kicker::before,.kicker::after{content:"";display:block;width:44px;height:3px;background:currentColor}
.title{font-weight:800;font-size:45px;letter-spacing:1.5px}
/* about */
.about-photo{left:172px;top:850px;width:344px;height:344px;border-radius:50%;background:radial-gradient(circle at 50% 40%,#c9a58c,#6b4a3a 60%,#2c2220)}
.about .kicker{left:598px;top:843px;color:var(--blue)}
.about .title{left:598px;top:880px;color:var(--blue)}
.about p{left:601px;top:950px;width:490px;font-size:15px;line-height:25.8px;color:#555}
.about .btn{left:599px;top:1163px;width:151px;height:39px;background:var(--blue);color:var(--white);font-size:15px}
/* services */
.services{left:0;top:1297px;width:1200px;height:629px;background:var(--green)}
.services .kicker{left:0;width:1200px;justify-content:center;top:66px;color:var(--white)}
.services .title{left:0;width:1200px;text-align:center;top:100px;color:var(--white)}
.svc-photo{top:190px;width:346px;height:306px}
.svc-head{top:326px;width:238px;height:73px;background:var(--blue);color:var(--white);padding:14px 0 0 30px}
.svc-head h3{font-size:18px;font-weight:700}
.svc-head small{font-size:13px}
.svc-body{top:399px;width:238px;height:151px;background:var(--white);padding:24px 16px 0 30px;font-size:14px;line-height:20px;color:#444}
.svc-body .more{display:flex;align-items:center;gap:10px;margin-top:10px;font-size:14px}
/* contact */
.contact{left:0;top:1926px;width:1200px;height:565px;background:linear-gradient(90deg,#f4f4f4,#e6e6e6 50%,#f4f4f4)}
.contact .title{left:0;width:1200px;text-align:center;top:75px;color:var(--ink)}
.info{left:134px;width:240px;text-align:center}
.info h4{color:var(--blue);font-size:20px;font-weight:500;margin-top:4px}
.info p{font-size:12px;line-height:15px;color:#333}
.divider-v{left:367px;top:205px;width:3px;height:238px;background:var(--blue)}
.field{background:var(--white);border:1px solid #ccc;border-radius:3px;font-size:13px;color:#333;padding:0 14px;display:flex;align-items:center}
.submit{left:419px;top:450px;width:100px;height:33px;background:var(--blue);color:var(--white);font-size:15px;font-weight:700;display:flex;align-items:center;justify-content:center;border-radius:2px}
/* reviews */
.reviews .kicker{left:0;width:1200px;justify-content:center;top:2552px;color:var(--ink)}
.reviews .title{left:0;width:1200px;text-align:center;top:2594px;color:var(--ink)}
.rev-back{top:2713px;width:390px;height:297px;background:var(--orange)}
.rev-card{top:2713px;width:360px;height:297px;background:var(--white);box-shadow:0 4px 18px rgba(0,0,0,.12);padding:76px 30px 0 26px}
.rev-card p{font-size:15px;line-height:25.8px;color:#555}
.rev-card h5{color:var(--green);font-size:20px;font-weight:500;margin-top:8px}
.rev-card .role{font-size:14px;color:#222;font-weight:500;display:flex;justify-content:space-between;margin-top:2px}
.stars{color:var(--green);font-size:19px;letter-spacing:1px}
.avatar{top:2663px;width:100px;height:100px;border-radius:50%;background:radial-gradient(circle at 50% 40%,#d2b49e,#7a5a48 70%);border:3px solid var(--white)}
.quote{top:2680px;font-size:70px;font-weight:800;color:#333;font-family:Georgia,serif;line-height:1}
.reviews .btn{left:525px;top:3057px;width:150px;height:38px;background:var(--orange);color:var(--white);font-size:15px}
/* footer */
.footer{left:0;top:3130px;width:1200px;height:562px}
.foot-mark{left:161px;top:3200px;width:76px;height:76px;border-radius:50%;border:3px solid var(--white)}
.foot-name{left:90px;top:3283px;width:240px;text-align:center;color:var(--white);font-size:19px;font-weight:700;line-height:20px}
.foot-name span{display:block;font-size:13px;letter-spacing:3px}
.footer h6{position:absolute;top:3376px;color:var(--white);font-size:21px;font-weight:700;letter-spacing:1.5px}
.foot-list{color:var(--white);font-size:15px;line-height:31px;font-weight:500}
.news-input{left:108px;top:3430px;width:252px;height:36px;background:var(--white);border-radius:3px;font-size:12px;font-weight:700;color:#222;padding:0 20px;display:flex;align-items:center;justify-content:space-between}
.foot-text{left:106px;top:3484px;width:300px;color:var(--white);font-size:15px;line-height:25.5px}
.foot-contact{left:886px;color:var(--white);font-size:15px;display:flex;gap:14px;align-items:flex-start;font-weight:500}
.foot-rule{left:112px;top:3621px;width:978px;height:1px;background:#777}
.copyright{left:0;top:3645px;width:1200px;text-align:center;color:var(--white);font-size:15px;letter-spacing:.5px}
</style>
</head>
<body>

<!-- top bar -->
<div class="abs topbar">
  <div class="abs item" style="left:112px">
    <svg width="16" height="16" viewBox="0 0 24 24" fill="none" stroke="#fff" stroke-width="2"><path d="M5 3h4l2 5-3 2a12 12 0 0 0 6 6l2-3 5 2v4a2 2 0 0 1-2 2A18 18 0 0 1 3 5a2 2 0 0 1 2-2z"/></svg>
    <span><b>Phone</b> +1 (555) 014 2736</span>
  </div>
  <div class="abs item" style="left:757px">
    <svg width="18" height="16" viewBox="0 0 24 20" fill="none" stroke="#fff" stroke-width="2"><rect x="2" y="3" width="20" height="14"/><path d="M2 3l10 8 10-8"/></svg>
    <span><b>E-mail</b> corinne@habbardmail.com</span>
  </div>
  <div class="abs social" style="left:1003px" role="img" aria-label="Professional network profile link"></div>
  <div class="abs social" style="left:1058px" role="img" aria-label="Social profile link"></div>
</div>

<!-- navigation -->
<nav class="abs nav">
  <a class="active" style="left:110px">Home</a>
  <a style="left:204px">About us</a>
  <a style="left:324px">Publications</a>
  <a style="left:793px">Media</a>
  <a style="left:888px">Services</a>
  <a style="left:1001px">Contact us</a>
</nav>
<div class="abs brand-cap"></div>
<div class="abs brand-mark"></div>
<div class="abs brand-name">CORINNE HABBARD<span>CONSULTING</span></div>

<!-- hero -->
<section class="abs hero">
  <div class="abs hero-photo" role="img" aria-label="Photo of a consultant in a blue sweater working on a laptop in a café"></div>
  <h1 class="abs">WELCOME TO<br>CORINNE HABBARD<br>CONSULTING</h1>
  <p class="abs">Lorem ipsum dolor sit amet, consectetur adipiscing elit, sed do eiusmod tempor incididunt ut labore et dolore magna aliqua. Ut enim ad minim veniam.</p>
  <div class="abs btn">GET STARTED</div>
  <svg class="abs" style="left:0;top:520px" width="1200" height="130" viewBox="0 0 1200 130">
    <path d="M0 120 L0 80 C150 30 420 40 700 90 C900 125 1080 100 1200 70 L1200 130 L0 130 Z" fill="#fff"/>
    <path d="M0 85 C150 40 420 45 700 100 C880 135 1060 110 1200 72 L1200 84 C1060 120 880 150 700 118 C420 62 150 55 0 92 Z" fill="#0a9be0"/>
    <path d="M0 76 C150 30 420 40 700 90 C900 125 1080 100 1200 66" fill="none" stroke="#0a9be0" stroke-width="2"/>
  </svg>
</section>

<!-- about -->
<section class="about">
  <svg class="abs" style="left:120px;top:800px" width="430" height="440" viewBox="0 0 430 440">
    <path d="M220 14 A205 205 0 1 1 20 240" fill="none" stroke="#0a9be0" stroke-width="3"/>
    <path d="M200 30 A192 192 0 1 1 24 190" fill="none" stroke="#0a9be0" stroke-width="9"/>
    <path d="M330 52 A192 192 0 0 1 410 200" fill="none" stroke="#6fc6ef" stroke-width="3"/>
  </svg>
  <div class="abs about-photo" role="img" aria-label="Portrait of the consulting firm founder"></div>
  <div class="abs kicker">LOREM IPSUM DOLOR</div>
  <h2 class="abs title">ABOUT US</h2>
  <p class="abs">Lorem ipsum dolor sit amet, consectetur adipiscing elit, sed do eiusmod tempor incididunt ut labore et dolore magna aliqua. Ut enim ad minim veniam, quis nostrud exercitation ullamco laboris nisi ut aliquip ex ea commodo consequat. Duis aute irure dolor in reprehenderit in voluptate velit esse cillum dolore eu fugiat nulla pariatur. Excepteur sint occaecat cupidatat non proident, sunt in culpa qui officia deserunt mollit anim id est laborum."</p>
  <div class="abs btn">READ MORE</div>
</section>

<!-- services -->
<section class="abs services">
  <div class="abs kicker">LOREM IPSUM DOLOR</div>
  <h2 class="abs title">OUR SERVICES</h2>
  <div class="abs svc-photo" style="left:112px;background:linear-gradient(135deg,#d9d9d9,#7a7a7a 60%,#3a3a3a)" role="img" aria-label="Photo of a consultant speaking at a desk with a laptop"></div>
  <div class="abs svc-head" style="left:285px"><h3>Consulting firm</h3><small>corinne habbard consulting</small></div>
  <div class="abs svc-body" style="left:285px">Lorem ipsum dolor sit amet, consectetur adipiscing elit, sed do eiusmod tempor incididunt .
    <div class="more">View Details <svg width="20" height="12" viewBox="0 0 20 12" fill="none" stroke="#444" stroke-width="1.6"><path d="M0 6h18M13 1l5 5-5 5"/></svg></div></div>
  <div class="abs svc-photo" style="left:741px;background:linear-gradient(135deg,#b7cde0,#6e8fb0 55%,#2e3f6a)" role="img" aria-label="Photo of a nurse in scrubs in a hospital ward"></div>
  <div class="abs svc-head" style="left:671px"><h3>Mindset and training</h3><small>of registered nurses</small></div>
  <div class="abs svc-body" style="left:671px">Lorem ipsum dolor sit amet, consectetur adipiscing elit, sed do eiusmod tempor incididunt .
    <div class="more">View Details <svg width="20" height="12" viewBox="0 0 20 12" fill="none" stroke="#444" stroke-width="1.6"><path d="M0 6h18M13 1l5 5-5 5"/></svg></div></div>
</section>

<!-- contact -->
<section class="abs contact">
  <h2 class="abs title">CONTACT US</h2>
  <div class="abs info" style="top:168px">
    <svg width="20" height="28" viewBox="0 0 20 28"><path d="M10 1a9 9 0 0 0-9 9c0 7 9 17 9 17s9-10 9-17a9 9 0 0 0-9-9z" fill="#0a9be0"/><circle cx="10" cy="10" r="3.5" fill="#fff"/></svg>
    <h4>Address</h4><p>United States,<br>corinne habbard consulting</p>
  </div>
  <div class="abs info" style="top:286px">
    <svg width="26" height="26" viewBox="0 0 24 24" fill="none" stroke="#0a9be0" stroke-width="2"><path d="M5 3h4l2 5-3 2a12 12 0 0 0 6 6l2-3 5 2v4a2 2 0 0 1-2 2A18 18 0 0 1 3 5a2 2 0 0 1 2-2z"/></svg>
    <h4>Phone</h4><p>+1(555)0142 736</p>
  </div>
  <div class="abs info" style="top:396px">
    <svg width="26" height="20" viewBox="0 0 26 20"><rect x="1" y="1" width="24" height="18" fill="#0a9be0"/><path d="M1 1l12 10 12-10" fill="none" stroke="#fff" stroke-width="2"/></svg>
    <h4>E-mail</h4><p>corinne@habbardmail.com</p>
  </div>
  <div class="abs divider-v"></div>
  <div class="abs field" style="left:419px;top:211px;width:291px;height:38px">First Name</div>
  <div class="abs field" style="left:740px;top:211px;width:290px;height:38px">Last Name</div>
  <div class="abs field" style="left:419px;top:271px;width:291px;height:39px">E-mail</div>
  <div class="abs field" style="left:740px;top:271px;width:290px;height:39px">Phone Number</div>
  <div class="abs field" style="left:419px;top:340px;width:611px;height:89px;align-items:flex-start;padding-top:14px">Message</div>
  <div class="abs submit">SUBMIT</div>
</section>

<!-- reviews -->
<section class="reviews">
  <div class="abs kicker">LOREM IPSUM DOLOR</div>
  <h2 class="abs title">CLIENT REVIEWS</h2>
  <div class="abs rev-back" style="left:146px;border-radius:120px 0 0 0"></div>
  <div class="abs rev-card" style="left:175px">
    <p>Lorem ipsum dolor sit amet, consectetur adipiscing elit, sed do eiusmod tempor incididunt ut labore et dolore magna aliqua. Ut enim ad minim veniam, quis nostrud exercitation ullamco laboris nisi ut aliquip ex ea commodo consequat.</p>
    <h5>Marisol</h5>
    <div class="role"><span>Consulting manager</span><span class="stars">★★★★★</span></div>
  </div>
  <div class="abs avatar" style="left:306px" role="img" aria-label="Client portrait"></div>
  <div class="abs quote" style="left:130px">“</div>

  <div class="abs rev-back" style="left:657px;border-radius:0 120px 0 0"></div>
  <div class="abs rev-card" style="left:657px">
    <p>Lorem ipsum dolor sit amet, consectetur adipiscing elit, sed do eiusmod tempor incididunt ut labore et dolore magna aliqua. Ut enim ad minim veniam, quis nostrud exercitation ullamco laboris nisi ut aliquip ex ea commodo consequat.</p>
    <h5>Delphine</h5>
    <div class="role"><span>Consulting manager</span><span class="stars">★★★★★</span></div>
  </div>
  <div class="abs avatar" style="left:786px" role="img" aria-label="Client portrait"></div>
  <div class="abs quote" style="left:1028px">”</div>
  <div class="abs btn">VIEW MORE</div>
</section>

<!-- footer -->
<footer class="abs footer">
  <svg class="abs" style="left:0;top:0" width="1200" height="562" viewBox="0 0 1200 562">
    <path d="M0 75 C200 -10 420 -10 640 50 C860 110 1020 110 1200 50 L1200 562 L0 562 Z" fill="#000"/>
    <path d="M0 66 C200 -20 420 -20 640 40 C860 100 1020 100 1200 42" fill="none" stroke="#000" stroke-width="3"/>
  </svg>
</footer>
<div class="abs foot-mark"></div>
<div class="abs foot-name">CORINNE HABBARD<span>CONSULTING</span></div>

<h6 style="left:108px">NEWSLETTER SIGNUP</h6>
<div class="abs news-input">Enter E-Mail Address
  <svg width="20" height="20" viewBox="0 0 24 24"><path d="M2 11L22 2l-9 20-2-9z" fill="#111"/></svg></div>
<p class="abs foot-text">Lorem ipsum dolor sit amet, consectetur adipiscing elit, sed do eiusmod tempor incididunt ut labore</p>

<h6 style="left:443px">ABOUT INFO</h6>
<div class="abs foot-list" style="left:443px;top:3419px">Home<br>About Us<br>Our services<br>Publications<br>Media</div>

<h6 style="left:650px">OUR SERVICES</h6>
<div class="abs foot-list" style="left:650px;top:3419px">Consulting firm<br>Mindset and training<br>of registered nurses</div>

<h6 style="left:886px;top:3378px">CONTACT US</h6>
<div class="abs foot-contact" style="top:3425px">
  <svg width="24" height="24" viewBox="0 0 24 24" fill="none" stroke="#fff" stroke-width="1.8"><path d="M5 3h4l2 5-3 2a12 12 0 0 0 6 6l2-3 5 2v4a2 2 0 0 1-2 2A18 18 0 0 1 3 5a2 2 0 0 1 2-2z"/></svg>
  <span style="padding-top:3px">+1 (555) 014 2736</span></div>
<div class="abs foot-contact" style="top:3472px">
  <svg width="22" height="18" viewBox="0 0 24 20" fill="none" stroke="#fff" stroke-width="1.8"><rect x="2" y="3" width="20" height="14"/><path d="M2 3l10 8 10-8"/></svg>
  <span>corinne@habbardmail.com</span></div>
<div class="abs foot-contact" style="top:3512px">
  <svg width="20" height="28" viewBox="0 0 20 28" fill="none" stroke="#fff" stroke-width="1.8"><path d="M10 1a9 9 0 0 0-9 9c0 7 9 17 9 17s9-10 9-17a9 9 0 0 0-9-9z"/><circle cx="10" cy="10" r="3.5"/></svg>
  <span style="line-height:20px">United States,<br>Corinne Habbard Consulting</span></div>

<div class="abs foot-rule"></div>
<div class="abs copyright">© Copyrights 2024 <b>CORINNE HABBARD CONSULTING</b> - All Rights Reserved.</div>

</body>
</html>
```